tinyTally Resource Book - 10 maths tasks to do outside

I need a 22 (11 pages back to back) page A6 sized book produced to standard for submission to professional printer. Needs to be as .pdf file showing guide lines and allowances for colour bleed. I have text already written and submitted as attachment in a Word file with margins set to A6 size. The theme of the materials is "Nature Play" so using lots of pictures from nature (Australia preferably) and showing lots of patterns in nature (rocks, leaves, flower petals etc). Some of the tasks refer to specific activities, such as "shadows" and "floating" so would be great to illustrate appropriately. The big emphasis is on learning outside the classroom, getting kids to engage actively with nature. I would like to see the pages as full colour - so not white background. The book itself will be spiral bound along the top edge so a margin of at least 1cm will be required at the top of each page (or the bottom of even numbered pages). Book will be printed on plastic laminated matte paper for outdoor use. Font size needs to be big enough to read. Fonts sizes, alignments and page numbers are all different at the moment and need to be standardised. One photo is included in a page as a sample if you can use it, otherwise disregard. Logo for Wattlebrook Numeracy Guild is also included to have as part of the acknowledgements at the back of the book.

Target Market(s)

Book is for early childhood and preschool teachers.

Industry/Entity Type

Education

Font styles to use
Sans Serif

Requirements
Must have
• Colour and appeal.
Nice to have
• Use of natural colours instead of bright catchy colours but that is your call.
Should not have
• American spelling

```html
<!DOCTYPE html>
<html lang="en">
<head>
<meta charset="utf-8">
<title>tinyTally – Big Bigger Biggest</title>
<link rel="stylesheet" href="https://fonts.googleapis.com/css2?family=Francois+One&family=Didact+Gothic&display=swap">
<style>
  :root {
    --paper: #ffffff;
    --navy: #2e3a93;
    --ink: #3b3530;
    --red: #d3252f;
    --wood-light: #e2c6a6;
    --wood-mid: #cfa27d;
    --wood-dark: #a97857;
    --bark: #8c8a88;
    --mark: #444;
  }
  html, body { margin: 0; padding: 0; overflow: hidden; }
  body { width: 825px; height: 1200px; background: var(--paper); position: relative; }
  .crop-marks { position: absolute; inset: 0; }
  .page {
    position: absolute; left: 50px; top: 56px; width: 726px; height: 1090px; overflow: hidden;
  }
  .page-photo {
    position: absolute; inset: 0;
    background:
      radial-gradient(ellipse 45% 25% at 72% 32%, var(--wood-dark) 0%, var(--wood-mid) 45%, transparent 75%),
      radial-gradient(ellipse 40% 22% at 68% 82%, #b07a57 0%, var(--wood-mid) 50%, transparent 80%),
      radial-gradient(ellipse 30% 18% at 20% 50%, var(--wood-mid) 0%, transparent 80%),
      linear-gradient(160deg, var(--wood-light) 0%, var(--wood-mid) 50%, var(--wood-light) 100%);
    opacity: .85;
  }
  .page-photo::after { content: ""; position: absolute; inset: 0; background: rgba(255,250,244,.25); }
  .text { position: absolute; margin: 0; }
  .task-title {
    left: 0; width: 726px; top: 100px; text-align: center;
    font: 42px/1 "Francois One", sans-serif; color: var(--navy);
    text-shadow: 2px 0 #fff, -2px 0 #fff, 0 2px #fff, 0 -2px #fff, 2px 2px #fff, -2px -2px #fff, 2px -2px #fff, -2px 2px #fff;
  }
  .outcome {
    left: 0; width: 726px; top: 126px; text-align: center;
    font: 30px/42px "Francois One", sans-serif; color: var(--navy);
    text-shadow: 1.5px 0 #fff, -1.5px 0 #fff, 0 1.5px #fff, 0 -1.5px #fff;
  }
  .lead {
    left: 66px; font: italic 24px/36px "Francois One", sans-serif; color: var(--navy);
    transform: skewX(-8deg); transform-origin: left;
  }
  .body-copy { left: 132px; font: 31px/43px "Didact Gothic", sans-serif; color: var(--ink); }
  .aims { left: 132px; top: 761px; list-style: none; padding: 0; font: 26px/35.5px "Didact Gothic", sans-serif; color: var(--ink); }
  .aims li { position: relative; padding-left: 20px; }
  .aims li::before {
    content: ""; position: absolute; left: 1px; top: 11px; width: 13px; height: 13px;
    background: var(--red); transform: rotate(45deg);
  }
  .page-number { position: absolute; left: 600px; top: 928px; width: 54px; height: 52px; }
</style>
</head>
<body>
  <svg class="crop-marks" width="825" height="1200" aria-hidden="true">
    <g stroke="var(--mark)" stroke-width="1">
      <line x1="69" y1="0" x2="69" y2="60"/><line x1="0" y1="74" x2="46" y2="74"/>
      <line x1="756" y1="0" x2="756" y2="60"/><line x1="779" y1="74" x2="825" y2="74"/>
      <line x1="69" y1="1140" x2="69" y2="1200"/><line x1="0" y1="1127" x2="46" y2="1127"/>
      <line x1="756" y1="1140" x2="756" y2="1200"/><line x1="779" y1="1127" x2="825" y2="1127"/>
    </g>
  </svg>

  <main class="page">
    <div class="page-photo" role="img" aria-label="Photograph of stacked cut log cross-sections showing tree rings"></div>

    <h1 class="text task-title" style="top:58px">2. Big Bigger Biggest</h1>
    <h2 class="text outcome" style="top:126px">EYLF – Outcome 2: Children are<br>connected with and contribute<br>to their world</h2>

    <p class="text lead" style="top:262px">Children become socially responsible and show<br>respect for the environment when they...</p>
    <p class="text body-copy" style="top:336px">explore relationships with other<br>living and non-living things and<br>observe, notice and respond to<br>change</p>

    <p class="text lead" style="top:505px">Educators promote this learning when they...</p>
    <p class="text body-copy" style="top:544px">provide children with access to a<br>range of natural materials in their<br>environment</p>

    <p class="text lead" style="top:672px">This task provides an opportunity to:</p>
    <ul class="text aims" style="top:706px">
      <li>explore the concepts of “change”<br>and “growth”</li>
      <li>discuss how growth happens</li>
      <li>make predictions about change</li>
      <li>formulate strategies for coping with<br>change</li>
    </ul>

    <svg class="page-number" viewBox="0 0 54 52" aria-label="Page 4">
      <polygon points="27,1 53,20 43,51 11,51 1,20" fill="var(--navy)"/>
      <text x="27" y="38" text-anchor="middle" font-family="Didact Gothic, sans-serif" font-size="28" fill="#fff">4</text>
    </svg>
  </main>
</body>
</html>
```